KRV Photography Business Card Design

I would like a business card designed in the shape of a camera.
Would like to see various camera designs. Would like to see what the card looks like in different colors. Would like to see which logo looks better on the various camera designs so please show me some with the white logo and some with the black logo. If you need a different file formats please let me know.
Project Deadline Extended Reason: My grandfather passed away and dealing with funeral plans so need to extend deadline. Added Tuesday, March 1, 2016
Project Deadline Extended
Reason: I just got back from out of town. My grandfather's passing was the primary focus for me these past few weeks and the funeral is over so now I will concentrate on picking my business card design. I really appreciate each designer who has taken the time to submit a design. Your effort has not gone unnoticed. I look forward to seeing more amazing designs.
Business
Contact Information for Business Card
Dorine
555-418-2706
https://www.facebook.com/krvphotographyfreelance/
MonaDorine@krv-photography.example

```html
<!DOCTYPE html>
<html lang="en">
<head>
<meta charset="utf-8">
<title>KRV Photography Business Card</title>
<link rel="stylesheet" href="https://fonts.googleapis.com/css2?family=Cinzel:wght@400&family=Roboto:wght@400;700&display=swap">
<style>
  :root {
    --backdrop: #ece9e4;
    --card: #1f1f1f;
    --gold: #e3b557;
    --text-light: #dcdcdc;
  }
  * { box-sizing: border-box; margin: 0; padding: 0; }
  html, body { width: 1200px; height: 1000px; overflow: hidden; }
  body { background: var(--backdrop); position: relative; font-family: "Roboto", sans-serif; }

  .card {
    position: absolute;
    left: 243px;
    width: 714px;
    height: 408px;
    background: var(--card);
    border-radius: 26px;
  }
  .card--front { top: 82px; }
  .card--back { top: 512px; }

  .brand-mark {
    position: absolute;
    width: 94px; height: 94px;
    border-radius: 50%;
    background: var(--gold);
  }
  .brand-name {
    position: absolute;
    font-family: "Cinzel", serif;
    font-weight: 400;
    font-size: 29px;
    letter-spacing: 0.6px;
    line-height: 1;
    color: var(--gold);
    white-space: nowrap;
  }
  .card--front .brand-mark { left: 482px; top: 37px; }
  .card--front .brand-name { right: 44px; top: 150px; }

  .holder-name {
    position: absolute;
    left: 44px; top: 219px;
    font-weight: 700;
    font-size: 26px;
    letter-spacing: 0.6px;
    color: var(--gold);
  }
  .contact-list {
    position: absolute;
    left: 44px; top: 263px;
    list-style: none;
  }
  .contact-item {
    display: flex;
    align-items: center;
    height: 31.5px;
    font-size: 16px;
    letter-spacing: 0.2px;
    color: var(--text-light);
  }
  .contact-icon {
    width: 14px; height: 14px;
    margin-right: 7px;
    flex: none;
  }

  .card--back .brand-mark { left: 310px; top: 131px; }
  .card--back .brand-name { left: 0; right: 0; text-align: center; top: 245px; }
  .website {
    position: absolute;
    left: 0; right: 0; top: 350px;
    text-align: center;
    font-size: 16px;
    letter-spacing: 0.2px;
    color: var(--text-light);
  }
</style>
</head>
<body>
  <section class="card card--front">
    <div class="brand-mark"></div>
    <div class="brand-name">KRV Photography</div>
    <h1 class="holder-name">DORINE</h1>
    <ul class="contact-list">
      <li class="contact-item">
        <svg class="contact-icon" viewBox="0 0 14 14" aria-hidden="true">
          <rect x="3.5" y="0.8" width="7" height="12.4" rx="1.2" fill="none" stroke="#e3b557" stroke-width="1.3"/>
          <circle cx="7" cy="11" r="0.8" fill="#e3b557"/>
        </svg>
        555-418-2706
      </li>
      <li class="contact-item">
        <svg class="contact-icon" viewBox="0 0 14 14" aria-hidden="true">
          <circle cx="7" cy="7" r="4.5" fill="#e3b557"/>
        </svg>
        krvphotographyfreelance
      </li>
      <li class="contact-item">
        <svg class="contact-icon" viewBox="0 0 14 14" aria-hidden="true">
          <rect x="1" y="3" width="12" height="8" fill="#e3b557"/>
          <path d="M1 3 L7 8 L13 3" fill="none" stroke="#1f1f1f" stroke-width="1.2"/>
        </svg>
        MonaDorine@krv-photography.example
      </li>
    </ul>
  </section>

  <section class="card card--back">
    <div class="brand-mark"></div>
    <div class="brand-name">KRV Photography</div>
    <div class="website">www.krv-photography.example</div>
  </section>
</body>
</html>
```